Business Card Design needed for start up company Halvora

In need of a new business card designed for a start up company based in Sydney, Halvora is a new start up innovative Company, our mission it to make property accessible for everyday Australian and to become the leading Real Estate platform in Australia. We want it to be fresh and clean.

Industry/Entity Type

Financial

Contact Information for Business Card

Section for Name
Section for Title

HALVORA - The Strength of Pooling
Mobile:
Direct:

Font styles to use
Sans Serif

Colors
33a6d7
0692cd
0255a3
ffffff

Requirements
Must have
• Logo, all business card details

```html
<!DOCTYPE html>
<html lang="en">
<head>
<meta charset="utf-8">
<title>Halvora Business Card</title>
<link rel="stylesheet" href="https://fonts.googleapis.com/css2?family=Source+Sans+3:wght@400;600;900&display=swap">
<style>
  :root {
    --backdrop: #3b322d;
    --card: #0d0d0e;
    --brand-blue: #0692cd;
    --accent-blue: #33a6d7;
    --divider: #0255a3;
    --white: #ffffff;
    --muted: #d9d9d9;
  }
  * { margin: 0; padding: 0; box-sizing: border-box; }
  html, body {
    width: 1200px; height: 844px; overflow: hidden;
    background: var(--backdrop);
    font-family: "Source Sans 3", "Helvetica Neue", Arial, sans-serif;
  }
  .stage {
    position: relative; width: 1200px; height: 844px;
    display: flex; align-items: center; justify-content: center; gap: 50px;
  }
  .card {
    position: relative; width: 520px; height: 300px;
    background: var(--card);
    box-shadow: 0 10px 30px rgba(0,0,0,.45);
  }
  /* Contact side */
  .mark-block {
    position: absolute; left: 50px; top: 62px; width: 150px;
    display: flex; flex-direction: column; align-items: center; gap: 12px;
  }
  .mark-circle {
    width: 130px; height: 130px; border-radius: 50%;
    background: var(--brand-blue);
  }
  .mark-name {
    color: var(--brand-blue); font-weight: 900; font-size: 20px; letter-spacing: 2px;
  }
  .divider {
    position: absolute; left: 250px; top: 60px; width: 1px; height: 180px;
    background: var(--divider); opacity: .7;
  }
  .details { position: absolute; left: 278px; top: 62px; color: var(--white); }
  .person-name {
    color: var(--accent-blue); font-weight: 600; font-size: 22px; letter-spacing: .5px;
  }
  .person-title { font-size: 15px; color: var(--muted); margin-top: 0; }
  .contact-list { list-style: none; margin-top: 30px; }
  .contact-list li {
    display: flex; align-items: center; gap: 10px;
    font-size: 16px; line-height: 22px; color: var(--white);
  }
  .contact-list svg { width: 13px; height: 13px; fill: var(--accent-blue); flex: none; }
  /* Logo side */
  .logo-lockup {
    position: absolute; left: 0; right: 0; top: 92px;
    display: flex; flex-direction: column; align-items: center;
  }
  .logo-row { display: flex; align-items: center; gap: 16px; }
  .logo-circle { width: 84px; height: 84px; border-radius: 50%; background: var(--white); }
  .logo-name {
    color: var(--white); font-weight: 900; font-size: 64px; letter-spacing: 1px; line-height: 1;
  }
  .tagline {
    margin-top: 14px; color: var(--brand-blue); font-weight: 600;
    font-size: 16px; letter-spacing: .8px; padding-left: 60px;
  }
</style>
</head>
<body>
<main class="stage">
  <section class="card card-contact">
    <div class="mark-block">
      <div class="mark-circle"></div>
      <span class="mark-name">HALVORA</span>
    </div>
    <div class="divider"></div>
    <div class="details">
      <h1 class="person-name">MARCUS REED</h1>
      <p class="person-title">Managing Director</p>
      <ul class="contact-list">
        <li><svg viewBox="0 0 16 16"><path d="M3 1h3l1.5 4-2 1.3a9 9 0 0 0 4.2 4.2L11 8.5l4 1.5v3a2 2 0 0 1-2 2A12 12 0 0 1 1 3a2 2 0 0 1 2-2z"/></svg>044-987 650 312</li>
        <li><svg viewBox="0 0 16 16"><path d="M4 0h8a1 1 0 0 1 1 1v14a1 1 0 0 1-1 1H4a1 1 0 0 1-1-1V1a1 1 0 0 1 1-1zm1 2v10h6V2zm3 11a1 1 0 1 0 0 2 1 1 0 0 0 0-2z"/></svg>044-987 650 313</li>
        <li><svg viewBox="0 0 16 16"><path d="M0 3h16v10H0zm1.5 1.5L8 9l6.5-4.5z"/></svg>hello@halvora.com</li>
        <li><svg viewBox="0 0 16 16"><circle cx="8" cy="8" r="7.5"/></svg>www.halvora.com</li>
      </ul>
    </div>
  </section>

  <section class="card card-logo">
    <div class="logo-lockup">
      <div class="logo-row">
        <div class="logo-circle"></div>
        <span class="logo-name">HALVORA</span>
      </div>
      <p class="tagline">THE STRENGTH OF POOLING</p>
    </div>
  </section>
</main>
</body>
</html>
```